Business Cards for new orthopaedic surgery practice

My husband and I are starting our own orthopaedic surgery practice. We are looking for a business card that is uniform, but one will have my name/title and the other will have his. You can just create one design with my name on it for now. But when I choose your design as the winning design I will ask that you add another copy with his name/title.

We are looking for classy, simple, elite all in one. We like dark blues/a little gold/yellow. Something that goes with our logo. We want our logo incorporated. Here is all the info you need:
Business name: RV Bone & Vitality Center
Location: 38517 North Willowmere Ave
Marlow Heights, FL 33490
Phone: 954-218-4063
Fax: 954-582-7341
Email: info@myrvbonecare.example

Names: Lydia Vance, M.D.
Board Certified Hand and Upper Extremity Surgeon

Ebo Dansu, M.D.
Board Certified Hip & Knee Replacement/General Orthopaedic Surgeon

Can decide what you want to put on the back. Maybe a slogan:
Grounded in Care. Centered on You

I am just going to upload our logo. The only thing is if we select you as the winning design, the location, and phone numbers may change. We will need your help to update that once fully solidified.

Industry/Entity Type

Medical

Contact Information for Business Card

Colors
0054AA
0677BA
7BADD7
CADEEF
E8F1F8
0094D4
00A9DD
6FCCEA
C7EBF8
E9F6FB

Requirements
Must have
• class, appeal,
Should not have
• We want to air on the side of masculine if we are looking at masculine vs. feminine feel. But we still want it classy, sophisticated, and something we will love

```html
<!DOCTYPE html>
<html lang="en">
<head>
<meta charset="utf-8">
<title>RV Bone &amp; Vitality Center – Business Card</title>
<link href="https://fonts.googleapis.com/css2?family=Montserrat:wght@400;500;600;700&display=swap" rel="stylesheet">
<style>
  :root {
    --navy: #1c2b52;
    --gold: #c39a4e;
    --paper: #ffffff;
    --stage: #e9ebef;
    --ink: #1c2b52;
    --white: #ffffff;
  }
  * { margin: 0; padding: 0; box-sizing: border-box; }
  html, body { width: 1200px; height: 897px; overflow: hidden; }
  body {
    background: var(--stage);
    font-family: "Montserrat", Arial, sans-serif;
    position: relative;
  }
  .card {
    position: absolute;
    left: 303px;
    width: 595px;
    height: 338px;
    border-radius: 18px;
    overflow: hidden;
    box-shadow: 0 6px 18px rgba(0,0,0,0.18);
  }
  .card-front { top: 92px; background: var(--paper); }
  .card-back { top: 469px; background: var(--navy); }

  .holder-name {
    position: absolute; left: 28px; top: 120px;
    font-size: 24px; font-weight: 700; letter-spacing: 1px;
    color: var(--gold); white-space: nowrap;
  }
  .holder-title {
    position: absolute; left: 28px; top: 150px;
    font-size: 14px; line-height: 17px; color: var(--ink);
  }
  .front-mark {
    position: absolute; left: 433px; top: 36px;
    width: 128px; height: 128px;
    border: 2px solid var(--navy); border-radius: 50%;
    display: flex; align-items: center; justify-content: center;
    text-align: center;
    font-size: 13px; font-weight: 600; line-height: 17px; color: var(--navy);
  }
  .divider {
    position: absolute; left: 28px; top: 200px;
    width: 535px; height: 2px; background: var(--gold);
  }
  .contact-list {
    position: absolute; left: 28px; top: 219px;
    list-style: none;
    font-size: 13.5px; line-height: 16.8px; color: var(--ink);
  }
  .contact-list li { display: flex; align-items: center; gap: 5px; white-space: nowrap; }
  .contact-list svg { width: 11px; height: 11px; flex: none; }
  .contact-list .accent { color: var(--gold); }
  .address {
    position: absolute; right: 32px; top: 236px;
    text-align: right; font-style: normal;
    font-size: 13.5px; line-height: 16.8px; color: var(--ink);
    white-space: nowrap;
  }
  .tagline-band {
    position: absolute; left: 0; bottom: 0;
    width: 100%; height: 35px; background: var(--navy);
    display: flex; align-items: center; justify-content: center;
    font-size: 16px; font-weight: 500; letter-spacing: 1.2px; color: var(--gold);
    white-space: nowrap;
  }
  .back-mark {
    position: absolute; left: 165px; top: 37px;
    width: 264px; height: 264px;
    border: 2px solid var(--gold); border-radius: 50%;
    display: flex; align-items: center; justify-content: center;
    text-align: center;
    font-size: 24px; font-weight: 600; line-height: 32px; letter-spacing: 1px;
    color: var(--white);
  }
</style>
</head>
<body>

<section class="card card-front">
  <div class="front-mark">RV Bone &amp;<br>Vitality<br>Center</div>

  <h1 class="holder-name">LYDIA VANCE, M.D</h1>
  <p class="holder-title">Board Certified Hand and<br>Upper Extremity Surgeon</p>

  <div class="divider"></div>

  <ul class="contact-list">
    <li>
      <svg viewBox="0 0 12 12" aria-hidden="true"><path d="M2.5 1 L4.5 1 L5.2 3.6 L3.9 4.6 C4.6 6 6 7.4 7.4 8.1 L8.4 6.8 L11 7.5 L11 9.5 C11 10.3 10.3 11 9.5 11 C5 11 1 7 1 2.5 C1 1.7 1.7 1 2.5 1 Z" fill="#c39a4e"/></svg>
      954-218-4063
    </li>
    <li>
      <svg viewBox="0 0 12 12" aria-hidden="true" fill="none" stroke="#c39a4e" stroke-width="1.1"><rect x="3" y="1" width="6" height="3"/><rect x="1" y="4" width="10" height="5" rx="1"/><rect x="3" y="7.5" width="6" height="3.5"/></svg>
      954-582-7341
    </li>
    <li>
      <svg viewBox="0 0 12 12" aria-hidden="true" fill="none" stroke="#c39a4e" stroke-width="1.1"><rect x="1" y="2.5" width="10" height="7"/><path d="M1 2.5 L6 6.5 L11 2.5"/></svg>
      info@myrvbonecare.example
    </li>
    <li>
      <svg viewBox="0 0 12 12" aria-hidden="true" fill="none" stroke="#c39a4e" stroke-width="1"><circle cx="6" cy="6" r="5"/><ellipse cx="6" cy="6" rx="2.2" ry="5"/><path d="M1 6 H11 M2 3.5 H10 M2 8.5 H10"/></svg>
      <span>www.<span class="accent">myrvbonecare</span>.example</span>
    </li>
  </ul>

  <address class="address">
    38517 North Willowmere<br>Ave Marlow Heights<br>FL 33490
  </address>

  <div class="tagline-band">Grounded in Care. Centered on You</div>
</section>

<section class="card card-back">
  <div class="back-mark">RV Bone &amp;<br>Vitality<br>Center</div>
</section>

</body>
</html>
```